Brintel Works - Fast, Efficient and Gas Mainteance for Domestic, Commercial and Industrial clients

We are in the process of purchasing a new business and would like to get a new logo and business card.
Business is a gas maintenance business that also does new gas installations.
Has been established since 1988.
Services include:
Install all types of gas appliances & equipment inc. hot water units
Maintain / repair / replace all types of gas appliances & equipment

Target Market(s)

Domestic, Commercial and Industrial clients

Industry/Entity Type

Business

Contact Information for Business Card

admin@brintelworks.com.au
07 3918 4726
Brintel Works PTY LTD

Logo Text

Gas Fitting & Plumbing Maintenance Specialists

Font styles to use
Sans Serif

Requirements
Must have
• Logo
• Business name, contact number, email address, web address
• Domestic | Commercial | Industrial Est Since 1988
Nice to have
• Possibly a black card with a flame logo to one side
Should not have
• Spelling errors

```html
<!DOCTYPE html>
<html lang="en">
<head>
<meta charset="utf-8">
<title>Brintel Works – Business Card</title>
<link rel="stylesheet" href="https://fonts.googleapis.com/css2?family=Open+Sans:wght@400;600;700&family=Great+Vibes&display=swap">
<style>
  :root {
    --backdrop: #3b3431;
    --card-black: #1c1c1c;
    --card-black-soft: #262626;
    --panel-white: #ececec;
    --brand-red: #e8331f;
    --ink-dark: #2b2b2b;
    --ink-grey: #8a8a8a;
    --ink-light: #f2f2f2;
    --mark-grey: #c9c9c9;
  }
  * { box-sizing: border-box; margin: 0; padding: 0; }
  html, body { width: 1200px; height: 780px; overflow: hidden; }
  body {
    background: var(--backdrop);
    font-family: "Open Sans", Arial, sans-serif;
    position: relative;
  }
  .card {
    position: absolute;
    width: 520px;
    height: 297px;
    top: 242px;
    border-radius: 4px;
    overflow: hidden;
    box-shadow: 0 14px 30px rgba(0,0,0,.45);
  }

  /* Front: contact side */
  .card--front { left: 50px; background: var(--card-black); }
  .front__head {
    height: 118px;
    background: var(--panel-white);
    border-bottom: 4px solid var(--brand-red);
    display: flex;
    align-items: center;
    padding: 0 24px;
    gap: 18px;
  }
  .brand-dot {
    width: 62px; height: 62px;
    border-radius: 50%;
    background: var(--mark-grey);
    flex: none;
  }
  .front__name {
    color: var(--brand-red);
    font-weight: 700;
    font-size: 27px;
    letter-spacing: .5px;
    line-height: 1.05;
  }
  .front__tagline {
    color: var(--ink-dark);
    font-weight: 700;
    font-size: 15px;
    margin-top: 3px;
  }
  .front__sectors {
    color: var(--ink-grey);
    font-size: 9.5px;
    margin-top: 4px;
    display: flex;
    align-items: baseline;
    gap: 10px;
  }
  .est {
    font-family: "Great Vibes", cursive;
    font-size: 15px;
    color: var(--ink-grey);
  }
  .contact-list {
    list-style: none;
    padding: 20px 0 0 40px;
  }
  .contact-list li {
    display: flex;
    align-items: center;
    gap: 12px;
    color: var(--ink-light);
    font-size: 15px;
    line-height: 28px;
  }
  .contact-icon {
    width: 13px; height: 13px;
    background: var(--brand-red);
    border-radius: 2px;
    display: flex; align-items: center; justify-content: center;
    flex: none;
  }
  .contact-icon svg { width: 9px; height: 9px; }

  /* Back: brand side */
  .card--back {
    left: 630px;
    background: radial-gradient(ellipse at 40% 40%, var(--card-black-soft), var(--card-black));
    display: flex;
    align-items: center;
    padding: 0 30px;
    gap: 24px;
  }
  .card--back .brand-dot { width: 120px; height: 120px; }
  .back__name {
    color: var(--brand-red);
    font-weight: 600;
    font-size: 36px;
    line-height: 1.05;
  }
  .back__legal {
    color: var(--ink-light);
    font-weight: 600;
    font-size: 12px;
    letter-spacing: 1px;
    margin-top: 4px;
  }
  .back__tagline {
    color: var(--ink-grey);
    font-size: 15px;
    margin-top: 6px;
  }
  .back__sectors {
    color: var(--ink-light);
    font-size: 11px;
    margin-top: 5px;
    display: flex;
    align-items: baseline;
    gap: 10px;
  }
  .back__sectors .est { color: var(--ink-light); font-size: 18px; }
</style>
</head>
<body>

<section class="card card--front" aria-label="Business card, contact side">
  <header class="front__head">
    <span class="brand-dot" aria-hidden="true"></span>
    <div class="front__brand">
      <h1 class="front__name">BRINTEL WORKS</h1>
      <p class="front__tagline">Gas fitting &amp; Plumbing Specialists</p>
      <p class="front__sectors">Domestic | Commercial | Industrial <span class="est">Est Since 1988</span></p>
    </div>
  </header>
  <ul class="contact-list">
    <li><span class="contact-icon"><svg viewBox="0 0 10 10"><path d="M2 1h2l1 2-1 1a5 5 0 0 0 2 2l1-1 2 1v2a1 1 0 0 1-1 1A8 8 0 0 1 1 2a1 1 0 0 1 1-1z" fill="#fff"/></svg></span>07 3918 4726</li>
    <li><span class="contact-icon"><svg viewBox="0 0 10 10"><rect x="1.5" y="3" width="7" height="5" fill="#fff"/><rect x="3" y="1" width="4" height="2" fill="#fff"/></svg></span>07 3918 4739</li>
    <li><span class="contact-icon"><svg viewBox="0 0 10 10"><circle cx="5" cy="5" r="3.6" fill="none" stroke="#fff" stroke-width="1.2"/><path d="M1.4 5h7.2M5 1.4v7.2" stroke="#fff" stroke-width="1"/></svg></span>www.brintelworks.com.au</li>
    <li><span class="contact-icon"><svg viewBox="0 0 10 10"><rect x="1" y="2.5" width="8" height="5.5" fill="#fff"/><path d="M1 2.5l4 3 4-3" fill="none" stroke="#e8331f" stroke-width="1"/></svg></span>admin@brintelworks.com.au</li>
    <li><span class="contact-icon"><svg viewBox="0 0 10 10"><path d="M5 9.2S2 6 2 4a3 3 0 0 1 6 0c0 2-3 5.2-3 5.2z" fill="#fff"/><circle cx="5" cy="4" r="1" fill="#e8331f"/></svg></span>PO Box 2846, Kallista Bay, QLD 4371</li>
  </ul>
</section>

<section class="card card--back" aria-label="Business card, brand side">
  <span class="brand-dot" aria-hidden="true"></span>
  <div class="back__brand">
    <h2 class="back__name">Brintel Works</h2>
    <p class="back__legal">PTY LTD</p>
    <p class="back__tagline">Gas Fitting &amp; Plumbing Specialists</p>
    <p class="back__sectors">Domestic | Commercial | Industrial <span class="est">Est Since 1988</span></p>
  </div>
</section>

</body>
</html>
```